Business Card for Vorla Parts Wholesale supplier

Hi There! I need a new business card for our company. We are specialized in selling Vorla parts, mostly we sell new LCD screens for Zelnar and Drelks. I would like to see that back in the design.

You can find the colors and logo's on our website: www.hartuvo.nl

Industry/Entity Type

Business

Contact Information for Business Card

My Details:
Tobias Lindqvist

Phone: 0031687203316
E-mail: Tobias@hartuvo.nl

Slogan: "Because Quality Matters"

Font styles to use
Sans Serif

Colors

Designer to choose colors to be used in the design.

Requirements
Must have
• A Black backside with the Hartuvo logo on it. The front side should be clean with only my contact details.
• But I'm also open for something really different or awesome!
Nice to have
• Remember that we are in the parts & repairing industry, So i'll be handing those business cards mainly to repair companies. Maybe you can do something with that thought :)

```html
<!DOCTYPE html>
<html lang="en">
<head>
<meta charset="UTF-8">
<title>Hartuvo Business Card</title>
<link href="https://fonts.googleapis.com/css2?family=Open+Sans:wght@400;600;700;800&display=swap" rel="stylesheet">
<style>
  :root {
    --stage: #e9e7e4;
    --card-black: #1f1f1f;
    --card-white: #ffffff;
    --brand-orange: #f26c22;
    --ink: #1a1a1a;
    --divider: #2b2b2b;
  }
  * { margin: 0; padding: 0; box-sizing: border-box; }
  html, body {
    width: 1200px; height: 780px; overflow: hidden;
    background: var(--stage);
    font-family: "Open Sans", Arial, sans-serif;
  }
  .canvas { position: relative; width: 1200px; height: 780px; }

  .card {
    position: absolute;
    width: 520px; height: 300px;
    box-shadow: 0 10px 28px rgba(0,0,0,0.18);
  }

  /* Back side */
  .card-back {
    left: 90px; top: 100px;
    background: var(--card-black);
    display: flex; align-items: center; justify-content: center;
  }
  .wordmark {
    display: flex; align-items: center; gap: 14px;
  }
  .wordmark-dot {
    width: 34px; height: 34px; border-radius: 50%;
    background: var(--brand-orange);
  }
  .wordmark-name {
    font-weight: 700; font-size: 58px; letter-spacing: 1px;
    color: #ffffff; line-height: 1;
  }

  /* Front side */
  .card-front {
    left: 620px; top: 380px;
    background: var(--card-white);
    color: var(--ink);
  }
  .front-brand {
    position: absolute; left: 40px; top: 104px; width: 170px;
    display: flex; flex-direction: column; align-items: center; gap: 10px;
  }
  .front-brand .wordmark-dot { width: 44px; height: 44px; }
  .front-brand-name {
    font-weight: 700; font-size: 30px; color: var(--brand-orange); line-height: 1;
  }
  .divider {
    position: absolute; left: 232px; top: 86px;
    width: 1px; height: 128px; background: var(--divider);
  }
  .contact {
    position: absolute; left: 258px; top: 92px;
  }
  .contact-name {
    font-weight: 700; font-size: 21px; color: var(--brand-orange);
    margin-bottom: 12px;
  }
  .contact-line {
    display: flex; align-items: center; gap: 7px;
    font-size: 16px; line-height: 22px;
  }
  .contact-icon { width: 16px; height: 16px; flex: none; }
  .contact-web { font-size: 16px; line-height: 22px; }
  .contact-web .accent { color: var(--brand-orange); }
  .slogan {
    position: absolute; left: 40px; top: 238px; width: 300px;
    font-weight: 600; font-size: 15px; text-align: center;
  }
</style>
</head>
<body>
<main class="canvas">
  <section class="card card-back" aria-label="Card back">
    <div class="wordmark">
      <span class="wordmark-dot"></span>
      <span class="wordmark-name">hartuvo</span>
    </div>
  </section>

  <section class="card card-front" aria-label="Card front">
    <div class="front-brand">
      <span class="wordmark-dot"></span>
      <span class="front-brand-name">hartuvo</span>
    </div>
    <div class="divider"></div>
    <div class="contact">
      <p class="contact-name">Tobias Lindqvist</p>
      <p class="contact-line">
        <svg class="contact-icon" viewBox="0 0 16 16" aria-hidden="true">
          <rect width="16" height="16" rx="3" fill="#f26c22"/>
          <path d="M5 3.5h2l.8 2.2-1.2.9a6 6 0 0 0 2.8 2.8l.9-1.2 2.2.8v2a1.2 1.2 0 0 1-1.3 1.2A8 8 0 0 1 3.8 4.8 1.2 1.2 0 0 1 5 3.5z" fill="#fff"/>
        </svg>
        0031687203316
      </p>
      <p class="contact-line">
        <svg class="contact-icon" viewBox="0 0 16 16" aria-hidden="true">
          <rect width="16" height="16" rx="3" fill="#f26c22"/>
          <rect x="3" y="4.5" width="10" height="7" fill="none" stroke="#fff" stroke-width="1.3"/>
          <path d="M3 4.5l5 4 5-4" fill="none" stroke="#fff" stroke-width="1.3"/>
        </svg>
        Tobias@hartuvo.nl
      </p>
      <p class="contact-web">www.<span class="accent">hartuvo</span>.nl</p>
    </div>
    <p class="slogan">Because Quality Matters</p>
  </section>
</main>
</body>
</html>
```